Business Card Design

We have recently seen two business cards that caught our attention and think the designs would work for us. We are an accounting firm that serves small businesses in a variety of industries. Attached are the two business card that inspired us along with very rough layouts. We would like to see a professional layout using our company information.

Industry/Entity Type

Accounting

Contact Information for Business Card

Company Name - Marlowe Thistle
Address - 4182 Orlanby Lane, Suite 610, Houston, TX 77093
713-555-0187 - Main
281-555-0342 - Fax

Team Member Names, emails and phone numbers (see attachment)

```html
<!DOCTYPE html>
<html lang="en">
<head>
<meta charset="utf-8">
<title>Marlowe Thistle – Business Card</title>
<link rel="stylesheet" href="https://fonts.googleapis.com/css2?family=Open+Sans:wght@400;600;700&display=swap">
<style>
  :root {
    --backdrop: #e6e4e1;
    --card-white: #ffffff;
    --card-shade: #f1f1f1;
    --charcoal: #3a3a3b;
    --arc-grey: #a7a7aa;
    --ink: #2b2b2b;
    --ink-soft: #3c3c3c;
    --mark-grey: #5a5a5c;
  }
  * { margin: 0; padding: 0; box-sizing: border-box; }
  html, body {
    width: 1200px; height: 900px; overflow: hidden;
    background: var(--backdrop);
    font-family: "Open Sans", Arial, sans-serif;
  }
  .sheet {
    width: 1200px; height: 900px;
    display: flex; flex-direction: column;
    align-items: center; justify-content: center; gap: 50px;
  }
  .card {
    position: relative;
    width: 630px; height: 360px;
    border-radius: 30px;
    overflow: hidden;
    box-shadow: 0 6px 18px rgba(0,0,0,0.18);
  }
  .card--front {
    background: radial-gradient(ellipse at 50% 40%, var(--card-white) 40%, var(--card-shade) 100%);
    display: flex; align-items: center; justify-content: center;
  }
  .card--back { background: var(--charcoal); }
  .card__shape { position: absolute; inset: 0; width: 100%; height: 100%; }

  .brand {
    display: flex; align-items: center; gap: 12px;
    color: var(--mark-grey);
    font-weight: 600;
    letter-spacing: 0.14em;
    text-transform: uppercase;
  }
  .brand__square { width: 14px; height: 14px; background: var(--mark-grey); }
  .card--front .brand { font-size: 30px; }

  .back-content {
    position: absolute; left: 0; right: 0; top: 118px;
    display: flex; flex-direction: column; align-items: center;
    color: var(--ink);
  }
  .back-content .brand { font-size: 26px; margin-bottom: 26px; }
  .person__name { font-size: 16px; font-weight: 700; color: var(--ink); }
  .person__role { font-size: 15px; color: var(--ink-soft); margin-bottom: 10px; }
  .contact { font-size: 12.5px; color: var(--ink-soft); text-align: center; line-height: 1.65; }
  .contact__label { font-weight: 700; color: var(--ink); }
  .contact__gap { display: inline-block; width: 14px; }
</style>
</head>
<body>
<main class="sheet">
  <section class="card card--front" aria-label="Card front">
    <div class="brand">
      <span class="brand__square"></span>
      <span class="brand__name">Marlowe Thistle</span>
    </div>
  </section>

  <section class="card card--back" aria-label="Card back">
    <svg class="card__shape" viewBox="0 0 630 360" preserveAspectRatio="none" aria-hidden="true">
      <path d="M0,360 L0,220 C50,95 200,52 330,52 C470,52 600,105 630,200 L630,360 Z" fill="var(--arc-grey)"/>
      <path d="M0,360 L0,236 C50,110 200,66 330,66 C465,66 592,118 622,212 L630,360 Z" fill="var(--card-white)"/>
    </svg>
    <div class="back-content">
      <div class="brand">
        <span class="brand__square"></span>
        <span class="brand__name">Marlowe Thistle</span>
      </div>
      <p class="person__name">Corin Abbott-Hale</p>
      <p class="person__role">Consultant</p>
      <div class="contact">
        <p><span class="contact__label">Add:</span> 4182 Orlanby Lane, Suite 610, Houston, TX 77093</p>
        <p><span class="contact__label">P:</span> 713-555-0187<span class="contact__gap"></span><span class="contact__label">F:</span> 281-555-0342</p>
        <p><span class="contact__label">E:</span> ledger@marlowethistle.com<span class="contact__gap"></span>www.marlowethistle.com</p>
      </div>
    </div>
  </section>
</main>
</body>
</html>
```